Brindlewood Racquet Club app

Design a sporting app that can, post news, post events, capture and show live scores, link at least 6 websites, other functions would be an advantage. Real tennis is also known as Royal tennis and Court tennis.
This would be like a sporting clubs app that gives live scores.

Colors

Designer to choose colors to be used in the design.

Requirements
Must have
• post news, post events, capture and show live scores, link at least 6 websites,
Nice to have
• Instructions on how to launch the app on apple and android

```html
<!DOCTYPE html>
<html lang="en">
<head>
<meta charset="utf-8">
<title>Brindlewood Racquet Club – Live Scores</title>
<link href="https://fonts.googleapis.com/css2?family=Open+Sans:wght@400;600;700;800&display=swap" rel="stylesheet">
<style>
  :root {
    --navy: #0a1590;
    --deep: #0c1a8a;
    --royal: #1e46f0;
    --royal-mid: #1a3ad8;
    --band-dark: #0f1f95;
    --white: #ffffff;
    --ink: #111111;
    --live-red: #e8141b;
    --accent: #1f4cf0;
    --line: rgba(255,255,255,0.55);
  }
  * { margin: 0; padding: 0; box-sizing: border-box; }
  html, body { width: 1200px; height: 2598px; overflow: hidden; }
  body {
    position: relative;
    font-family: "Open Sans", sans-serif;
    color: var(--white);
    background: linear-gradient(160deg, #0a0f85 0%, #1530c8 30%, #0d1d99 55%, #1a3ddc 80%, #1233c8 100%);
  }
  .abs { position: absolute; }
  .status-time { left: 80px; top: 22px; font-size: 22px; font-weight: 600; }
  .status-icons { right: 88px; top: 24px; }
  .ghost-title {
    left: 0; width: 1200px; text-align: center; top: 70px;
    font-size: 190px; font-weight: 800; letter-spacing: 4px;
    color: rgba(5,10,90,0.35); white-space: nowrap; overflow: hidden;
  }
  .page-title {
    left: 0; width: 1200px; text-align: center; top: 120px;
    font-size: 108px; font-weight: 700; letter-spacing: -1px; line-height: 1;
  }
  .score-card {
    left: 94px; top: 406px; width: 1023px; height: 445px;
    background: var(--white); border-radius: 54px; color: var(--ink);
  }
  .club-tab {
    left: 525px; top: 313px; width: 165px; height: 120px;
    background: var(--white); border-radius: 20px 20px 0 0;
    display: flex; flex-direction: column; align-items: center; justify-content: center; gap: 8px;
  }
  .club-mark { width: 34px; height: 34px; border-radius: 50%; background: var(--accent); }
  .club-name { font-size: 20px; font-weight: 700; color: var(--accent); }
  .live-badge {
    left: 67px; top: 487px; width: 82px; height: 41px; background: var(--live-red);
    font-size: 22px; font-weight: 700; display: flex; align-items: center; justify-content: center; letter-spacing: 1px;
  }
  .player-photo {
    width: 228px; height: 228px; border-radius: 50%;
    box-shadow: 0 10px 20px rgba(0,0,0,0.2);
  }
  .photo-left { left: 165px; top: 486px; background: radial-gradient(circle at 50% 45%, #ffe54a 0%, #f8cf00 60%, #1a8aa0 100%); }
  .photo-right { left: 811px; top: 486px; background: radial-gradient(circle at 50% 45%, #e2b89a 0%, #7a8a5a 55%, #3d4a2c 100%); }
  .player-name { top: 760px; width: 300px; text-align: center; font-size: 22px; font-weight: 500; color: var(--ink); }
  .name-left { left: 130px; }
  .name-right { left: 785px; }
  .match-info { left: 400px; width: 420px; text-align: center; color: var(--ink); }
  .time-label { top: 527px; font-size: 22px; font-weight: 700; color: var(--accent); }
  .time-value { top: 570px; font-size: 22px; font-weight: 500; }
  .score { top: 618px; font-size: 88px; font-weight: 700; color: var(--accent); line-height: 1; }
  .tournament { top: 731px; font-size: 22px; font-weight: 500; }
  .divider { left: 0; top: 936px; width: 1200px; height: 1px; background: var(--line); }
  .tabs { left: 0; top: 969px; width: 1200px; height: 58px; }
  .tab { position: absolute; top: 0; height: 58px; display: flex; align-items: center; justify-content: center; font-size: 22px; font-weight: 600; }
  .tab.active { background: var(--royal); border-radius: 16px; }
  .set-table { left: 0; top: 1062px; width: 1200px; }
  .set-row { position: relative; height: 70px; }
  .row-head { background: var(--royal); height: 70px; }
  .row-a { background: var(--band-dark); }
  .row-b { background: var(--royal); }
  .set-row span { position: absolute; top: 0; height: 100%; display: flex; align-items: center; font-size: 22px; }
  .row-player { left: 30px; font-weight: 600; }
  .cell { justify-content: center; width: 78px; }
  .col-lines { position: absolute; left: 0; top: 0; width: 1200px; height: 209px; pointer-events: none; }
  .match-time {
    height: 70px; background: var(--deep); display: flex; align-items: center; justify-content: center;
    font-size: 22px;
  }
  .section-title { left: 0; width: 1200px; text-align: center; top: 1385px; font-size: 76px; font-weight: 700; line-height: 1; letter-spacing: -1px; }
  .ghost-sub { left: 0; width: 1200px; text-align: center; top: 1335px; font-size: 170px; font-weight: 800; color: rgba(5,10,90,0.25); white-space: nowrap; overflow: hidden; }
  .fixture { left: 0; width: 1200px; display: flex; align-items: center; }
  .fixture.light { background: linear-gradient(90deg, #1c40e6, #2049e8); }
  .fixture.dark { background: linear-gradient(90deg, #0e1b92, #142aa8); }
  .fixture-date { width: 249px; text-align: center; line-height: 1; }
  .fixture-day { display: block; font-size: 70px; font-weight: 700; letter-spacing: -2px; }
  .fixture-month { display: block; font-size: 31px; margin-top: 2px; }
  .fixture-text { font-size: 32px; line-height: 48px; }
</style>
</head>
<body>
  <div class="abs status-time">9:41</div>
  <svg class="abs status-icons" width="112" height="24" viewBox="0 0 112 24" aria-label="Signal, wifi and battery">
    <rect x="0" y="14" width="4" height="6" fill="#fff"/>
    <rect x="6" y="11" width="4" height="9" fill="#fff"/>
    <rect x="12" y="7" width="4" height="13" fill="#fff"/>
    <rect x="18" y="3" width="4" height="17" fill="#fff"/>
    <path d="M36 8 a14 14 0 0 1 20 0 M39 12 a9 9 0 0 1 14 0" stroke="#fff" stroke-width="3" fill="none"/>
    <circle cx="46" cy="17" r="3" fill="#fff"/>
    <rect x="72" y="3" width="36" height="17" rx="4" stroke="#fff" stroke-width="2" fill="none"/>
    <rect x="75" y="6" width="30" height="11" rx="2" fill="#fff"/>
    <rect x="109" y="9" width="3" height="6" fill="#fff"/>
  </svg>

  <div class="abs ghost-title">LIVE SCORES</div>
  <h1 class="abs page-title">LIVE SCORES</h1>

  <section class="abs score-card"></section>
  <div class="abs club-tab">
    <span class="club-mark"></span>
    <span class="club-name">Brindlewood</span>
  </div>
  <div class="abs live-badge">LIVE</div>

  <div class="abs player-photo photo-left" role="img" aria-label="Portrait photo of player Laura Gofman holding a racquet"></div>
  <div class="abs player-photo photo-right" role="img" aria-label="Portrait photo of player Tammy Young holding a racquet"></div>
  <div class="abs player-name name-left">LAURA GOFMAN</div>
  <div class="abs player-name name-right">TAMMY YOUNG</div>

  <div class="abs match-info time-label">TIME</div>
  <div class="abs match-info time-value">03 Dec 14:00</div>
  <div class="abs match-info score">5 - 4</div>
  <div class="abs match-info tournament">Open Tennis Tournament</div>

  <div class="abs divider"></div>

  <nav class="abs tabs">
    <span class="tab active" style="left:71px;width:156px;">Summary</span>
    <span class="tab" style="left:280px;width:110px;">Stats</span>
    <span class="tab" style="left:450px;width:182px;">Point By Point</span>
    <span class="tab" style="left:700px;width:124px;">Preview</span>
    <span class="tab" style="left:880px;width:102px;">H2H</span>
    <span class="tab" style="left:1040px;width:96px;">Draw</span>
  </nav>

  <div class="abs set-table">
    <div class="set-row row-head">
      <span class="cell" style="left:653px;">S</span>
      <span class="cell" style="left:732px;">1</span>
      <span class="cell" style="left:810px;">2</span>
      <span class="cell" style="left:887px;">3</span>
      <span class="cell" style="left:962px;">4</span>
      <span class="cell" style="left:1040px;">5</span>
      <span class="cell" style="left:1117px;">6</span>
    </div>
    <div class="set-row row-a">
      <span class="row-player">LAURA GOFMAN</span>
      <span class="cell" style="left:568px;">40</span>
      <span class="cell" style="left:653px;">2</span>
      <span class="cell" style="left:732px;">6</span>
      <span class="cell" style="left:810px;">6</span>
      <span class="cell" style="left:887px;">4</span>
    </div>
    <div class="set-row row-b">
      <span class="row-player" style="left:33px;">TAMMY YOUNG</span>
      <span class="cell" style="left:566px;">40</span>
      <span class="cell" style="left:651px;">2</span>
      <span class="cell" style="left:729px;">6</span>
      <span class="cell" style="left:807px;">6</span>
      <span class="cell" style="left:884px;">4</span>
    </div>
    <svg class="col-lines" viewBox="0 0 1200 209">
      <g stroke="#ffffff" stroke-opacity="0.7" stroke-width="1.5">
        <line x1="653" y1="0" x2="653" y2="209"/>
        <line x1="732" y1="0" x2="732" y2="209"/>
        <line x1="810" y1="0" x2="810" y2="209"/>
        <line x1="888" y1="0" x2="888" y2="209"/>
        <line x1="960" y1="0" x2="960" y2="209"/>
        <line x1="1040" y1="0" x2="1040" y2="209"/>
        <line x1="1116" y1="0" x2="1116" y2="209"/>
      </g>
    </svg>
    <div class="match-time">MATCH TIME 2:06&nbsp;&nbsp;0:37&nbsp;&nbsp;0:40&nbsp;&nbsp;0:49</div>
  </div>

  <div class="abs ghost-sub">MATCHES</div>
  <h2 class="abs section-title">NEXT MATCHES</h2>

  <div class="abs fixture light" style="top:1516px;height:199px;">
    <div class="fixture-date" style="width:220px;"><span class="fixture-day">25</span><span class="fixture-month">Dec</span></div>
    <div class="fixture-text" style="margin-left:29px;">Gofman – VS – Young<br>14:00, Laura Gofman - Tammy Young</div>
  </div>
  <div class="abs fixture dark" style="top:1715px;height:200px;">
    <div class="fixture-date" style="width:238px;"><span class="fixture-day">25</span><span class="fixture-month">Dec</span></div>
    <div class="fixture-text" style="margin-left:11px;">McHall – VS – Ferry<br>12:00, Sandy McHall - Lisa Ferry</div>
  </div>
  <div class="abs fixture light" style="top:1915px;height:202px;">
    <div class="fixture-date" style="width:238px;"><span class="fixture-day">25</span><span class="fixture-month">Dec</span></div>
    <div class="fixture-text" style="margin-left:11px;">Gofman – VS – Lee<br>14:00, Laura Gofman - Amy Lee</div>
  </div>
  <div class="abs fixture dark" style="top:2117px;height:206px;">
    <div class="fixture-date" style="width:238px;"><span class="fixture-day">25</span><span class="fixture-month">Dec</span></div>
    <div class="fixture-text" style="margin-left:11px;">Ferry – VS – Young<br>12:00, Lisa Ferry - Tammy Young</div>
  </div>
  <div class="abs fixture light" style="top:2323px;height:200px;">
    <div class="fixture-date" style="width:238px;"><span class="fixture-day">25</span><span class="fixture-month">Dec</span></div>
    <div class="fixture-text" style="margin-left:11px;">Ferry – VS – Young<br>12:00, Lisa Ferry - Tammy Young</div>
  </div>
</body>
</html>
```